Employment Agency Website Design

We are working with an employment agency in California.

Some sites to use for content/competitors and inspiration:

https://www.pinecrestjobs.com/us/en
https://www.velmorusa.com
https://www.dravenworks.us
https://www.quillora.com/en
https://www.tomvalusa.com
https://www.fernstaffing.com

Thank you for taking the time to consider designing a website for us. We are web developers based in Stockton, CA, USA. Most of our projects go through the same process. Understanding this process may help you win a project with us. We custom-code all of our websites in-house. We don’t have any requirements as to what tools you use for your design, but we prefer Figma files. For any design that we label as four-stars, we send it to the client for review. The client picks the final design they want us to use. Once we complete this process, we will continue to show additional clients all the four-star sites and purchase them later. Your designs will have multiple chances to sell. For better chances of success, we ask that you follow these guidelines.

IMAGES:
If you use any images or icons in the design, we ask that you have a link to the asset so we can purchase the image/icon. Most of the designs we submit do not have the customer’s images on them unless they have some great images. Be creative; show us the feeling you are trying to portray with your image choices. Use any royalty-free site you choose. We subscribe to Adobe and mainly use their images, but we can purchase images outside of Adobe. PLEASE NOTE: we will not submit designs to clients with watermarks on the images.

FONTS:
We ask that you identify the fonts used in the design. This can be done in a message if you want. We typically use Google Fonts and Adobe Fonts.

CONTENT:
We're always open to different content and ideas. We often submit designs with stock images so the client can see our vision. We typically take pictures after the website launch to use their images with our vision. Lorem Ipsum is fine for paragraphs, but we ask that you write the headers in correct English. We want to be able to show the vision and identify the sections of the website.

INSPIRATION:
We typically add a couple of links in the brief of websites we like to help you get started in your design.

REVISIONS:
We do not often ask for revisions of the designs unless we see something in the design that may not appeal to the client. If there are slight changes that we want to make, we do that in the development process.

FEEDBACK:
We rarely give feedback on designs during the design process. We are working on many website projects and do not have the time to provide feedback. We usually respond if your request is well thought out and asks specific questions, but a note asking “feedback, please” usually goes unanswered.

```html
<!DOCTYPE html>
<html lang="en">
<head>
<meta charset="utf-8">
<title>Brightpath Talent — Employment Agency</title>
<link href="https://fonts.googleapis.com/css2?family=Roboto:wght@400;500;700&display=swap" rel="stylesheet">
<style>
:root{
  --red:#c41e35;
  --red-dark:#a8172b;
  --ink:#111111;
  --text:#555a60;
  --muted:#8a8f95;
  --pink:#f3e3e6;
  --line:#dcdde0;
  --white:#ffffff;
  --footer:#161617;
}
*{box-sizing:border-box;margin:0;padding:0}
html,body{width:1200px;height:5208px;overflow:hidden}
body{font-family:'Roboto',sans-serif;color:var(--ink);background:var(--white);position:relative}
.abs{position:absolute}
a{color:inherit;text-decoration:none}

/* header */
.site-header{position:absolute;left:0;top:0;width:1200px;height:82px;z-index:5}
.brand{position:absolute;left:112px;top:18px;display:flex;align-items:center;gap:8px}
.brand-mark{width:22px;height:22px;background:var(--red);border-radius:4px}
.brand-name{font-size:28px;font-weight:500;color:var(--ink);letter-spacing:-0.5px}
.brand-tag{position:absolute;left:160px;top:55px;font-size:11px;color:var(--muted)}
.main-nav{position:absolute;left:402px;top:32px;display:flex;gap:26px;font-size:13px;font-weight:500}
.main-nav a.active{color:var(--red)}
.btn{display:inline-flex;align-items:center;justify-content:center;font-weight:500;color:#fff;border-radius:3px}
.btn-dark{background:var(--ink)}
.btn-red{background:var(--red)}

/* hero */
.hero{position:absolute;left:0;top:0;width:1200px;height:800px;background:linear-gradient(180deg,#f6f6f7 0%,#efeff0 70%,#ffffff 100%);overflow:hidden}
.hero-title{position:absolute;left:162px;top:220px;font-size:52px;font-weight:700}
.hero-sub{position:absolute;left:162px;top:292px;font-size:19px;color:#444}
.hero-arrow{position:absolute;width:34px;height:34px;border-radius:50%;background:var(--ink);display:flex;align-items:center;justify-content:center}

.diamond{position:absolute;width:138px;height:138px;transform:rotate(45deg)}
.diamond-label{position:absolute;width:160px;text-align:center;color:#fff;font-size:16px}

/* partners */
.partner{position:absolute;top:880px;height:52px;border-radius:26px;background:#e4e5e7}

/* section headings */
.h2{font-size:50px;font-weight:700;color:var(--ink)}
.copy{font-size:13.5px;line-height:25.5px;color:var(--text);text-align:justify}

.stat{position:absolute;top:2370px;width:140px;height:60px;border-radius:4px;padding:10px 14px}
.stat b{display:block;font-size:21px;font-weight:700;color:#1b2b6b}
.stat span{font-size:9px;color:#333}

/* services */
.svc{position:absolute;width:212px;height:212px}
.svc-card{position:absolute;inset:0;background:#fff;border-radius:42px;transform:rotate(45deg);box-shadow:0 10px 30px rgba(40,40,60,.12)}
.svc-accent{position:absolute;inset:0;border-radius:42px;transform:rotate(45deg) translate(var(--dx),var(--dy));border:0 solid var(--c)}
.svc-body{position:absolute;left:11px;width:190px;top:48px;text-align:center;font-size:12.5px;line-height:20px;color:var(--muted)}
.svc-body svg{display:block;margin:0 auto 14px}

/* blog */
.blog{position:absolute;left:0;top:3572px;width:1200px;height:745px;background:var(--red);overflow:hidden}
.blog-card{position:absolute;top:190px;width:302px;height:438px;background:#fff;border-radius:4px;padding:8px;text-align:center}
.blog-img{height:235px;border-radius:2px}
.blog-date{display:inline-flex;align-items:center;gap:5px;margin-top:20px;padding:4px 14px;background:#fbe7ea;border-radius:14px;font-size:11px;color:#555}
.blog-title{margin-top:16px;font-size:21px;font-weight:500}
.blog-text{margin:12px 20px 0;font-size:12.5px;line-height:25px;color:var(--muted)}
.blog-more{display:inline-block;margin-top:12px;font-size:12.5px;font-weight:700;color:var(--red);text-decoration:underline}

/* contact */
.field{position:absolute;border:1px solid var(--line);border-radius:3px;font-size:11px;color:#666;padding:14px 16px}

/* footer */
.site-footer{position:absolute;left:0;top:4810px;width:1200px;height:398px;background:linear-gradient(180deg,#2a2a2c 0%,var(--footer) 45%,#0e0e0f 100%);color:#fff}
.f-head{position:absolute;top:92px;font-size:22px;font-weight:500}
.f-list{position:absolute;top:135px;font-size:13px;line-height:26px;list-style:none}
</style>
</head>
<body>

<!-- HERO -->
<section class="hero">
  <div class="abs" role="img" aria-label="Flowing dotted wave graphic" style="left:60px;top:340px;width:620px;height:300px;background:radial-gradient(ellipse at 60% 50%,rgba(150,150,155,.28),rgba(240,240,241,0) 68%)"></div>
  <div class="abs" style="left:820px;top:0;width:380px;height:260px;background:linear-gradient(135deg,rgba(226,194,200,.35),rgba(255,255,255,0))"></div>
  <div class="abs" role="img" aria-label="Smiling young professional holding an open laptop" style="left:565px;top:100px;width:445px;height:565px;background:linear-gradient(180deg,#d9dbe2 0%,#b9c3e6 55%,#8f9bd0 100%);border-radius:180px 180px 20px 20px"></div>
  <h1 class="hero-title">Brightpath Talent</h1>
  <p class="hero-sub">We are an employment agency in California.</p>
  <a class="btn btn-red abs" style="left:163px;top:336px;width:150px;height:38px;font-size:12px;font-weight:700">BOOK A CALL</a>
  <span class="hero-arrow" style="left:75px;top:303px"><svg width="10" height="10" viewBox="0 0 10 10"><path d="M6.5 1.5 3 5l3.5 3.5" stroke="#fff" stroke-width="1.6" fill="none"/></svg></span>
  <span class="hero-arrow" style="left:1088px;top:303px"><svg width="10" height="10" viewBox="0 0 10 10"><path d="M3.5 1.5 7 5 3.5 8.5" stroke="#fff" stroke-width="1.6" fill="none"/></svg></span>
</section>

<!-- HEADER -->
<header class="site-header">
  <div class="brand"><span class="brand-mark"></span><span class="brand-name">brightpath talent</span></div>
  <span class="brand-tag">The future of work</span>
  <nav class="main-nav">
    <a class="active">Home</a><a>About</a><a>Services</a><a>Resources</a><a>Blog</a>
  </nav>
  <a class="btn btn-dark abs" style="left:776px;top:21px;width:152px;height:41px;font-size:13px">Contact Us</a>
  <a class="btn btn-red abs" style="left:940px;top:21px;width:148px;height:41px;font-size:13px">Book A Call</a>
</header>

<!-- FEATURE DIAMONDS -->
<div class="diamond" style="left:241px;top:601px;background:var(--ink)"></div>
<div class="diamond" style="left:433px;top:601px;background:var(--red)"></div>
<div class="diamond" style="left:625px;top:601px;background:var(--ink)"></div>
<div class="diamond" style="left:817px;top:601px;background:var(--red)"></div>
<svg class="abs" style="left:286px;top:622px" width="48" height="48" viewBox="0 0 48 48" fill="none" stroke="#fff" stroke-width="2"><path d="M24 4 38 10v10c0 9-6 16-14 20C16 36 10 29 10 20V10z"/><path d="m17 21 5 5 9-10"/></svg>
<svg class="abs" style="left:478px;top:622px" width="48" height="48" viewBox="0 0 48 48" fill="none" stroke="#fff" stroke-width="2"><circle cx="24" cy="16" r="9"/><path d="M8 40c4-8 10-11 16-11s12 3 16 11"/></svg>
<svg class="abs" style="left:670px;top:622px" width="48" height="48" viewBox="0 0 48 48" fill="none" stroke="#fff" stroke-width="2"><circle cx="24" cy="20" r="10"/><circle cx="24" cy="20" r="4"/><path d="M6 42h36M12 42c0-6 5-10 12-10s12 4 12 10"/></svg>
<svg class="abs" style="left:862px;top:622px" width="48" height="48" viewBox="0 0 48 48" fill="none" stroke="#fff" stroke-width="2"><circle cx="24" cy="22" r="14"/><path d="M10 22h28M24 8c5 5 5 23 0 28M24 8c-5 5-5 23 0 28M14 42h20"/></svg>
<span class="diamond-label" style="left:230px;top:690px">Lorem ipsum</span>
<span class="diamond-label" style="left:422px;top:690px">Lorem ipsum</span>
<span class="diamond-label" style="left:614px;top:690px">Lorem ipsum</span>
<span class="diamond-label" style="left:806px;top:690px">Lorem ipsum</span>

<!-- PARTNERS -->
<svg class="abs" style="left:46px;top:896px" width="12" height="14" viewBox="0 0 12 14"><path d="M8 2 3 7l5 5" stroke="#555" stroke-width="1.5" fill="none"/></svg>
<svg class="abs" style="left:1138px;top:896px" width="12" height="14" viewBox="0 0 12 14"><path d="M4 2l5 5-5 5" stroke="#555" stroke-width="1.5" fill="none"/></svg>
<div class="partner" style="left:142px;width:86px"></div>
<div class="partner" style="left:318px;width:64px"></div>
<div class="partner" style="left:466px;width:104px"></div>
<div class="partner" style="left:648px;width:66px"></div>
<div class="partner" style="left:800px;width:82px"></div>
<div class="partner" style="left:966px;width:104px"></div>

<!-- ABOUT -->
<svg class="abs" style="left:0;top:1040px" width="560" height="990" viewBox="0 0 560 990">
  <defs><linearGradient id="aboutPhoto" x1="0" y1="0" x2="1" y2="1"><stop offset="0" stop-color="#cfd3d8"/><stop offset=".5" stop-color="#8d8f96"/><stop offset="1" stop-color="#3a3d44"/></linearGradient></defs>
  <polygon points="255,40 515,295 515,705 255,955 -10,705 -10,295" fill="var(--pink)" stroke="var(--pink)" stroke-width="60" stroke-linejoin="round"/>
  <polygon points="255,125 500,365 500,660 255,890 -10,660 -10,365" fill="url(#aboutPhoto)" stroke="url(#aboutPhoto)" stroke-width="40" stroke-linejoin="round" role="img" aria-label="Business colleagues smiling during a meeting at a table"/>
  <circle cx="45" cy="200" r="28" fill="var(--red)"/>
</svg>
<h2 class="h2 abs" style="left:579px;top:1345px">About Us</h2>
<p class="copy abs" style="left:579px;top:1420px;width:510px">Lorem ipsum dolor sit amet, consectetur adipiscing elit, sed do eiusmod tempor incididunt ut labore et dolore magna aliqua. Ut enim ad minim veniam, quis nostrud exercitation ullamco laboris nisi ut aliquip ex ea commodo consequat. Duis aute irure dolor in reprehenderit in voluptate velit esse cillum dolore eu fugiat nulla pariatur. Excepteur sint occaecat cupidatat non proident, sunt in culpa qui officia deserunt mollit anim id est laborum. Lorem ipsum dolor sit amet, consectetur adipiscing elit, sed do eiusmod tempor incididunt ut labore et dolore magna aliqua. Ut enim ad minim veniam, quis nostrud exercitation ullamco laboris nisi ut aliquip ex ea commodo consequat.</p>
<a class="btn btn-red abs" style="left:579px;top:1672px;width:150px;height:40px;font-size:13px">Learn More</a>

<!-- RESOURCES -->
<svg class="abs" style="left:660px;top:1850px" width="540" height="960" viewBox="0 0 540 960">
  <defs><linearGradient id="resPhoto" x1="0" y1="0" x2="1" y2="1"><stop offset="0" stop-color="#b7a79a"/><stop offset=".5" stop-color="#5a6478"/><stop offset="1" stop-color="#2c3650"/></linearGradient></defs>
  <polygon points="285,40 560,280 560,680 285,920 50,700 50,270" fill="var(--pink)" stroke="var(--pink)" stroke-width="60" stroke-linejoin="round"/>
  <polygon points="285,110 560,340 560,640 285,860 70,640 70,320" fill="url(#resPhoto)" stroke="url(#resPhoto)" stroke-width="40" stroke-linejoin="round" role="img" aria-label="Cheerful businessmen applauding and shaking hands"/>
  <circle cx="495" cy="175" r="28" fill="var(--red)"/>
</svg>
<h2 class="h2 abs" style="left:111px;top:2095px">Resources</h2>
<p class="copy abs" style="left:111px;top:2170px;width:511px">Lorem ipsum dolor sit amet, consectetur adipiscing elit, sed do eiusmod tempor incididunt ut labore et dolore magna aliqua. Ut enim ad minim veniam, quis nostrud exercitation ullamco laboris nisi ut aliquip ex ea commodo consequat. Duis aute irure dolor in reprehenderit in voluptate velit esse cillum dolore eu fugiat nulla pariatur. Excepteur sint occaecat cupidatat non proident, sunt in culpa qui officia deserunt mollit anim id est laborum. Lorem ipsum dolor sit amet, consectetur adipiscing elit, sed do eiusmod tempor</p>
<div class="stat" style="left:112px;background:#fdeef0"><b>33%+</b><span>More great-fit candidates</span></div>
<div class="stat" style="left:262px;background:#fdf4e6"><b>25%+</b><span>Less money for every hire</span></div>
<div class="stat" style="left:412px;background:#e9f8ef"><b>20M+</b><span>Jobs powered by our team</span></div>
<a class="btn btn-red abs" style="left:112px;top:2458px;width:150px;height:39px;font-size:13px">Learn More</a>

<!-- SERVICES -->
<h2 class="h2 abs" style="left:0;top:2855px;width:1200px;text-align:center">Our Services</h2>
<p class="abs" style="left:230px;top:2930px;width:740px;text-align:center;font-size:13.5px;line-height:25.5px;color:var(--text)">Lorem ipsum dolor sit amet, consectetur adipiscing elit, sed do eiusmod tempor incididunt ut labore et dolore magna aliqua. Ut enim ad minim veniam, quis nostrud exercitation ullamco laboris nisi ut aliquip</p>

<div class="svc" style="left:157px;top:3076px">
  <div class="svc-accent" style="--c:var(--ink);--dx:0px;--dy:-8px;border-top-width:6px"></div>
  <div class="svc-card"></div>
  <div class="svc-body"><svg width="52" height="52" viewBox="0 0 64 64" fill="var(--red-dark)"><circle cx="32" cy="14" r="7"/><circle cx="14" cy="20" r="6"/><circle cx="50" cy="20" r="6"/><path d="M20 38c0-7 5-12 12-12s12 5 12 12z"/><circle cx="32" cy="46" r="10" fill="none" stroke="var(--red-dark)" stroke-width="5"/><path d="M4 36c0-6 4-9 10-9 3 0 5 1 6 2l-3 7zM60 36c0-6-4-9-10-9-3 0-5 1-6 2l3 7z"/></svg>Lorem ipsum dolor sit amet, consectetur adipiscing elit, sed do eiusmod tempor</div>
</div>
<div class="svc" style="left:605px;top:3076px">
  <div class="svc-accent" style="--c:var(--red);--dx:-8px;--dy:0px;border-left-width:6px"></div>
  <div class="svc-card"></div>
  <div class="svc-body"><svg width="52" height="52" viewBox="0 0 64 64" fill="var(--red-dark)"><rect x="8" y="30" width="10" height="26"/><rect x="22" y="16" width="10" height="40"/><rect x="36" y="36" width="10" height="20"/><path d="M48 6a12 12 0 1 1-12 12h12z"/><rect x="4" y="56" width="56" height="4"/></svg>Lorem ipsum dolor sit amet, consectetur adipiscing elit, sed do eiusmod tempor</div>
</div>
<div class="svc" style="left:379px;top:3227px">
  <div class="svc-accent" style="--c:var(--red);--dx:0px;--dy:8px;border-bottom-width:6px"></div>
  <div class="svc-card"></div>
  <div class="svc-body"><svg width="52" height="52" viewBox="0 0 64 64" fill="var(--red-dark)"><circle cx="32" cy="10" r="6"/><path d="M22 28c0-6 4-10 10-10s10 4 10 10z"/><circle cx="14" cy="40" r="6"/><path d="M4 58c0-6 4-10 10-10s10 4 10 10z"/><circle cx="50" cy="40" r="6"/><path d="M40 58c0-6 4-10 10-10s10 4 10 10z"/></svg>Lorem ipsum dolor sit amet, consectetur adipiscing elit, sed do eiusmod tempor</div>
</div>
<div class="svc" style="left:829px;top:3227px">
  <div class="svc-accent" style="--c:var(--ink);--dx:0px;--dy:-8px;border-top-width:6px"></div>
  <div class="svc-card"></div>
  <div class="svc-body"><svg width="52" height="52" viewBox="0 0 64 64" fill="var(--red-dark)"><path d="M10 40 30 14l10 6 14-10 4 8-14 14-10 12-16 6z"/></svg>Lorem ipsum dolor sit amet, consectetur adipiscing elit, sed do eiusmod tempor</div>
</div>

<!-- BLOG -->
<section class="blog">
  <div class="abs" style="left:1015px;top:80px;width:148px;height:148px;border-radius:50%;background:rgba(255,255,255,.14)"></div>
  <div class="abs" style="left:48px;top:140px;width:160px;height:160px;border-radius:50%;background:rgba(255,255,255,.12)"></div>
  <div class="abs" style="left:850px;top:400px;width:520px;height:520px;border-radius:50%;background:rgba(255,255,255,.1)"></div>
  <h2 class="h2 abs" style="left:0;top:90px;width:1200px;text-align:center;color:#fff">Latest Blog Post</h2>
  <article class="blog-card" style="left:111px">
    <div class="blog-img" role="img" aria-label="Two professionals shaking hands across a desk" style="background:linear-gradient(135deg,#c9b3a2,#6d5a52)"></div>
    <span class="blog-date"><svg width="10" height="10" viewBox="0 0 10 10"><rect x="0.5" y="1.5" width="9" height="8" rx="1" fill="var(--red)"/></svg>Jan 20,2023</span>
    <h3 class="blog-title">Duis aute irure dolor</h3>
    <p class="blog-text">Lorem ipsum dolor sit amet, consectetur adipiscing elit, sed do eiusmod</p>
    <a class="blog-more">Read More</a>
  </article>
  <article class="blog-card" style="left:449px">
    <div class="blog-img" role="img" aria-label="Celebrating office team giving thumbs up" style="background:linear-gradient(135deg,#a9acb3,#3f4350)"></div>
    <span class="blog-date"><svg width="10" height="10" viewBox="0 0 10 10"><rect x="0.5" y="1.5" width="9" height="8" rx="1" fill="var(--red)"/></svg>Jan 20,2023</span>
    <h3 class="blog-title">Duis aute irure dolor</h3>
    <p class="blog-text">Lorem ipsum dolor sit amet, consectetur adipiscing elit, sed do eiusmod</p>
    <a class="blog-more">Read More</a>
  </article>
  <article class="blog-card" style="left:786px">
    <div class="blog-img" role="img" aria-label="Colleagues reviewing documents at a meeting" style="background:linear-gradient(135deg,#dcdcde,#4a4c54)"></div>
    <span class="blog-date"><svg width="10" height="10" viewBox="0 0 10 10"><rect x="0.5" y="1.5" width="9" height="8" rx="1" fill="var(--red)"/></svg>Jan 20,2023</span>
    <h3 class="blog-title">Duis aute irure dolor</h3>
    <p class="blog-text">Lorem ipsum dolor sit amet, consectetur adipiscing elit, sed do eiusmod</p>
    <a class="blog-more">Read More</a>
  </article>
</section>

<!-- CONTACT -->
<h2 class="h2 abs" style="left:133px;top:4392px;line-height:60px">We’re excited to<br>talk with you!</h2>
<p class="abs" style="left:133px;top:4526px;width:420px;font-size:13.5px;line-height:25.5px;color:var(--text)">Lorem ipsum dolor sit amet, consectetur adipiscing elit, sed do eiusmod tempor incididunt ut labore et dolore magna aliqua. Ut enim ad minim veniam, quis nostrud exercitation ullamco laboris nisi ut aliquip</p>
<div class="field" style="left:621px;top:4412px;width:214px;height:43px">Name</div>
<div class="field" style="left:853px;top:4412px;width:215px;height:43px">Phone</div>
<div class="field" style="left:621px;top:4477px;width:447px;height:43px">Email</div>
<div class="field" style="left:621px;top:4543px;width:447px;height:102px">Message</div>
<a class="btn btn-red abs" style="left:621px;top:4668px;width:214px;height:42px;font-size:12px;font-weight:700">SUBMIT NOW</a>

<!-- FOOTER -->
<footer class="site-footer" role="contentinfo">
  <div class="abs" role="img" aria-label="Dark city skyline at dusk" style="left:0;top:0;width:1200px;height:398px;background:linear-gradient(180deg,rgba(80,80,84,.35),rgba(0,0,0,0) 60%)"></div>
  <h4 class="f-head" style="left:110px">About Us</h4>
  <p class="abs" style="left:110px;top:136px;width:290px;font-size:13px;line-height:21px">Lorem ipsum dolor sit amet, consectetur adipiscing elit, sed do eiusmod tempor inci didunt ut labore et dolore magna aliqua. Ut enim ad minim veniam, quis nostrud exercit ation ullamco laboris nisi ut aliquip ex ea commodo consequat.</p>
  <h4 class="f-head" style="left:500px">Quick Links</h4>
  <ul class="f-list" style="left:500px"><li>Home</li><li>About</li><li>Services</li><li>Blog</li><li>Resources</li></ul>
  <h4 class="f-head" style="left:705px">Support</h4>
  <ul class="f-list" style="left:705px"><li>Privacy policy</li><li>Terms of services</li><li>Support</li><li>Faq</li><li>Contact us</li></ul>
  <h4 class="f-head" style="left:887px">Contact</h4>
  <svg class="abs" style="left:884px;top:140px" width="12" height="14" viewBox="0 0 12 14"><path d="M6 1a4 4 0 0 1 4 4c0 3-4 8-4 8S2 8 2 5a4 4 0 0 1 4-4z" fill="var(--red)"/><circle cx="6" cy="5" r="1.5" fill="#fff"/></svg>
  <p class="abs" style="left:918px;top:135px;width:180px;font-size:13px;line-height:24px">123,Lorem ipsum dolor sit consectetur adip</p>
  <svg class="abs" style="left:884px;top:214px" width="13" height="13" viewBox="0 0 13 13"><path d="M2 1h3l1 3-2 1a7 7 0 0 0 4 4l1-2 3 1v3c-6 0-10-4-10-10z" fill="var(--red)"/></svg>
  <p class="abs" style="left:918px;top:208px;font-size:13px">+1 888 888 8888</p>
  <svg class="abs" style="left:884px;top:240px" width="14" height="11" viewBox="0 0 14 11"><rect width="14" height="11" rx="1" fill="var(--red)"/><path d="m1 1 6 5 6-5" stroke="#fff" fill="none"/></svg>
  <p class="abs" style="left:918px;top:234px;font-size:13px">info@brightpathtalent.com</p>
  <p class="abs" style="left:0;top:328px;width:1200px;text-align:center;font-size:13px">© Copyrights 2023 Company name | All Rights Reserved</p>
</footer>

</body>
</html>
```